Design the Business card for NetVaultic

Business card required for a professional Cyber Security business.
Company Logo and Icon has already been provided however I would like other options for the logo and icon to compare to. Alternatively, please refine/enhance the image of the logo.icon I have already provided.

If you are going to use the provided logo and icon, I was thinking that the company raised Logo on White background would serve well on the front of the card. See attached. AND, a large company raised stand-alone icon to appear on black background on the back of the card with tagline 'Cyber Risk Management, Governance and Consulting' or 'Cyber Security for your Business' See attached.
Alternatively, provide your own design for the logo and icon.

Target Market(s)

Enterprise, Government, Financial.

Contact Information for Business Card

Tavin Orloweth
Founder and CEO

Email Address
Mobile Number
Website URL
LinkedIn URL

Logo Text

NetVaultic - see attached example of logo

Font styles to use
Other font styles liked:
• Berlin Sans FB

Requirements
Must have
• Clean large and bold icon on the back with tagline.
• Horizontal alignment,
Nice to have
• Round edges.
• Raised Logo/Icon
Should not have
• An unprofessional look and feel.

```html
<!DOCTYPE html>
<html lang="en">
<head>
<meta charset="utf-8">
<title>NetVaultic Business Card</title>
<link href="https://fonts.googleapis.com/css2?family=Roboto:wght@400&family=Roboto+Condensed:wght@500;700&family=Cabin:wght@500&display=swap" rel="stylesheet">
<style>
  :root {
    --stage: #262626;
    --card-light: #f3f3f3;
    --card-dark: #1b1c1e;
    --brand-blue: #1a70c0;
    --brand-yellow: #f2b705;
    --tag-blue: #4a6fc8;
    --tag-yellow: #f4c20d;
    --ink: #555555;
  }
  * { margin: 0; padding: 0; box-sizing: border-box; }
  html, body { width: 1200px; height: 960px; overflow: hidden; background: var(--stage); }
  .canvas { position: relative; width: 1200px; height: 960px; }

  .card { position: absolute; left: 322px; width: 598px; height: 342px; border-radius: 18px; }
  .card--front { top: 108px; background: var(--card-light); }
  .card--back { top: 494px; background: var(--card-dark); }

  .wordmark {
    position: absolute; left: 36px; top: 46px;
    display: flex; align-items: center; gap: 10px;
    font-family: "Roboto Condensed", sans-serif; font-weight: 700;
    font-size: 34px; color: var(--brand-blue);
  }
  .wordmark__dot { width: 44px; height: 44px; border-radius: 50%; background: var(--brand-blue); }

  .contact-list {
    position: absolute; left: 34px; top: 226px; list-style: none;
    font-family: "Roboto", sans-serif; font-size: 14.5px; color: var(--ink);
  }
  .contact-list li { display: flex; align-items: center; gap: 9px; height: 19.5px; }
  .contact-list svg { width: 13px; height: 13px; flex: none; }

  .person { position: absolute; right: 30px; top: 254px; text-align: right; font-family: "Roboto Condensed", sans-serif; }
  .person__name { font-weight: 700; font-size: 23px; color: var(--brand-blue); line-height: 1.1; }
  .person__role { font-weight: 500; font-size: 15.5px; color: var(--brand-yellow); line-height: 1.2; }

  .back-mark {
    position: absolute; left: 0; right: 0; top: 96px;
    display: flex; justify-content: center; align-items: center; gap: 14px;
    font-family: "Roboto Condensed", sans-serif; font-weight: 700;
    font-size: 44px; color: var(--tag-blue);
  }
  .back-mark__dot { width: 60px; height: 60px; border-radius: 50%; background: var(--tag-blue); }

  .tagline {
    position: absolute; left: 0; right: 0; top: 274px; text-align: center;
    font-family: "Cabin", sans-serif; font-weight: 500; font-size: 18px; color: var(--tag-blue);
  }
  .tagline__accent { color: var(--tag-yellow); }
</style>
</head>
<body>
<main class="canvas">
  <section class="card card--front">
    <div class="wordmark"><span class="wordmark__dot"></span>NetVaultic</div>

    <ul class="contact-list">
      <li>
        <svg viewBox="0 0 13 13"><rect x="3" y="0.5" width="7" height="12" rx="1.2" fill="none" stroke="var(--brand-blue)" stroke-width="1.4"/><circle cx="6.5" cy="10.3" r="0.8" fill="var(--brand-blue)"/></svg>
        555 014 2738
      </li>
      <li>
        <svg viewBox="0 0 13 13"><rect x="0.5" y="2.5" width="12" height="8" fill="var(--brand-blue)"/><path d="M0.5 2.5 L6.5 7 L12.5 2.5" fill="none" stroke="#fff" stroke-width="1"/></svg>
        tavin@netvaultic.com
      </li>
      <li>
        <svg viewBox="0 0 13 13"><circle cx="6.5" cy="6.5" r="6" fill="var(--brand-blue)"/><ellipse cx="6.5" cy="6.5" rx="2.5" ry="6" fill="none" stroke="#fff" stroke-width="0.9"/><line x1="0.5" y1="6.5" x2="12.5" y2="6.5" stroke="#fff" stroke-width="0.9"/></svg>
        www.netvaultic.com
      </li>
      <li>
        <svg viewBox="0 0 13 13"><circle cx="6.5" cy="6.5" r="6" fill="var(--brand-blue)"/></svg>
        netvaultic
      </li>
    </ul>

    <div class="person">
      <p class="person__name">TAVIN ORLOWETH</p>
      <p class="person__role">FOUNDER &amp; CEO</p>
    </div>
  </section>

  <section class="card card--back">
    <div class="back-mark"><span class="back-mark__dot"></span>NetVaultic</div>
    <p class="tagline">Cyber Risk Management, <span class="tagline__accent">Governance &amp; Consulting</span></p>
  </section>
</main>
</body>
</html>
```